Medical Clinic Group Looking for Website Design

We own and operate medical clinics and are looking looking to revamp our website. Our current website is www.brightpathcareclinics.ca We need our website to be more functional, user friendly, and easier to maintain.

```html
<!DOCTYPE html>
<html lang="en">
<head>
<meta charset="utf-8">
<title>Brightpath Care Clinics</title>
<link href="https://fonts.googleapis.com/css2?family=Lexend:wght@400;500;600;700&family=Lato:wght@400;700&display=swap" rel="stylesheet">
<style>
:root{
  --teal:#2fd0dc;
  --teal-dark:#1fb9c6;
  --ink:#111418;
  --text:#2b2f33;
  --grey:#8a8d90;
  --light:#f3f5f6;
  --black:#050607;
  --white:#ffffff;
}
*{box-sizing:border-box;margin:0;padding:0}
html,body{width:1200px;height:3560px;overflow:hidden}
body{position:relative;background:var(--white);font-family:"Lato",sans-serif;color:var(--text)}
.abs{position:absolute}
.head{font-family:"Lexend",sans-serif;color:var(--ink);font-weight:600}
.eyebrow{font-family:"Lexend",sans-serif;color:var(--teal);font-weight:600;font-size:15px;letter-spacing:5px;text-transform:uppercase}
.btn{position:absolute;background:var(--teal);color:var(--ink);font-family:"Lexend",sans-serif;font-weight:600;font-size:19px;display:flex;align-items:center;justify-content:center;border-radius:4px;box-shadow:0 5px 10px rgba(0,0,0,.18)}

/* hero */
.hero-rim{left:0;top:0;width:1200px;height:664px;background:var(--teal);border-radius:0 0 170px 170px}
.hero{left:0;top:0;width:1200px;height:648px;background:linear-gradient(90deg,#f4f5f6 0%,#eef0f1 45%,#e7e9ea 100%);border-radius:0 0 160px 160px;overflow:hidden}
.hero-photo{left:560px;top:0;width:640px;height:648px;background:linear-gradient(120deg,#e9eaeb 0%,#cfd3d6 40%,#8f7563 60%,#3a6fb8 85%,#2b5aa1 100%)}
.hero-fade{left:420px;top:0;width:320px;height:648px;background:linear-gradient(90deg,#eff1f2,rgba(239,241,242,0))}
.brand{left:110px;top:28px;display:flex;align-items:center;gap:14px}
.brand .mark{width:40px;height:40px;border:3px solid #7d8083;border-radius:6px}
.brand .name{font-family:"Lexend",sans-serif;font-size:40px;font-weight:400;color:var(--teal);line-height:1}
.nav{left:547px;top:42px;display:flex;gap:38px;font-family:"Lexend",sans-serif;font-size:16px;color:var(--ink)}
.nav .active{color:var(--teal);font-weight:600;text-decoration:underline}
.nav-cta{left:957px;top:30px;width:132px;height:52px;font-size:16px}
.hero-eyebrow{left:111px;top:196px}
.hero-title{left:111px;top:222px;font-size:39px;line-height:47px;font-weight:700;white-space:nowrap}
.hero-sub{left:111px;top:373px;font-size:13.5px;line-height:24px;color:#3a3d40;font-weight:700;width:400px}
.hero-btn{left:111px;top:431px;width:153px;height:57px}

/* about */
.about-art{left:110px;top:760px;width:478px;height:326px;display:flex;align-items:center;justify-content:center;gap:22px}
.about-art .sq{width:70px;height:70px;background:var(--teal)}
.about-art .word{font-family:"Lexend",sans-serif;font-size:60px;font-weight:400;color:#8c8f92}
.about-eyebrow{left:622px;top:745px}
.about-title{left:623px;top:772px;font-size:32px;white-space:nowrap}
.about-copy{left:623px;top:816px;width:465px;font-size:15.5px;line-height:27.5px;text-align:justify;color:#3a3d40}
.about-copy p+p{margin-top:27px}
.about-btn{left:623px;top:1052px;width:153px;height:58px}

/* services */
.svc-eyebrow{left:111px;top:1182px}
.svc-title{left:111px;top:1208px;font-size:35px}
.svc-arrows{left:975px;top:1212px;display:flex;gap:40px}
.card{top:1293px;height:471px;overflow:hidden}
.card .photo{position:absolute;inset:0}
.card .shade{position:absolute;inset:0;background:linear-gradient(180deg,rgba(0,0,0,0) 45%,rgba(0,0,0,.72) 100%)}
.card .txt{position:absolute;left:57px;right:30px;bottom:26px;color:var(--white)}
.card h3{font-family:"Lato",sans-serif;font-weight:700;font-size:25px;line-height:32px}
.card p{font-size:14.5px;line-height:24px;margin-top:8px}
.card svg{margin-top:8px}
.c1{left:0;width:390px}.c2{left:405px;width:391px}.c3{left:810px;width:390px}
.c1 .photo{background:linear-gradient(135deg,#2a3547,#8b7b6c 45%,#c9b59f 60%,#2c3140)}
.c2 .photo{background:linear-gradient(135deg,#d9dbdc,#b9b1ab 40%,#e8e4e1 70%,#6d6a6a)}
.c3 .photo{background:linear-gradient(135deg,#e6e8ea,#c4bfba 45%,#a8adb3 70%,#7c8187)}

/* happening */
.hap-eyebrow{left:110px;top:1833px}
.hap-title{left:109px;top:1858px;font-size:35px;white-space:nowrap}
.hap-copy{left:111px;top:1904px;width:520px;font-size:16px;line-height:26px;color:#222}
.hap-list{left:111px;top:1985px;width:560px;list-style:none;font-size:16px;color:#222}
.hap-list li{display:flex;gap:8px;line-height:29px;margin-bottom:5.5px}
.hap-list li svg{flex:none;margin-top:9px}
.hap-btn{left:111px;top:2197px;width:256px;height:59px}
.hap-photo{left:677px;top:1825px;width:470px;height:408px;background:radial-gradient(ellipse at 50% 45%,#c9c3bd 0%,#e9e7e5 45%,#ffffff 75%)}
.dot{width:34px;height:34px;border-radius:50%;background:var(--white);border:1px solid #d5d7d9;display:flex;align-items:center;justify-content:center}

/* faq */
.faq{left:0;top:2321px;width:1200px;height:740px;background:linear-gradient(180deg,#3bd3de,#2ccad6)}
.faq-eyebrow{left:0;top:2380px;width:1200px;text-align:center;color:var(--ink);font-size:15px}
.faq-title{left:0;top:2403px;width:1200px;text-align:center;font-size:35px}
.q{left:110px;width:978px;border:2px solid #1c3b40;border-radius:36px;display:flex;align-items:center;padding:0 30px;font-size:20px;color:#133035}
.q .label{flex:1;margin-left:10px}
.q .pm{width:44px;height:40px;background:var(--white);border-radius:3px;display:flex;align-items:center;justify-content:center}
.q1{top:2472px;height:68px}
.q3{top:2783px;height:68px}
.qopen{left:110px;top:2557px;width:978px;height:211px;background:#eef9fa;border-radius:30px;box-shadow:0 4px 12px rgba(0,0,0,.15);padding:16px 30px 0}
.qopen .row{display:flex;align-items:center;font-size:20px;color:#133035;padding-bottom:16px;border-bottom:1px solid #9aa5a7}
.qopen .pm{width:44px;height:40px;background:var(--teal);border-radius:3px;display:flex;align-items:center;justify-content:center}
.qopen p{font-size:14.5px;line-height:26px;color:#3b4244;margin-top:14px}
.view-btn{left:524px;top:2896px;width:152px;height:58px;background:var(--white);font-size:19px}

/* footer */
.foot-rim{left:0;top:3012px;width:1200px;height:548px;background:var(--white);border-radius:170px 170px 0 0}
.foot-rim2{left:0;top:3018px;width:1200px;height:542px;background:var(--teal);border-radius:166px 166px 0 0}
.foot{left:0;top:3030px;width:1200px;height:530px;background:var(--black);border-radius:156px 156px 0 0}
.sub-title{left:235px;top:3128px;font-size:30px;color:var(--white)}
.sub-form{left:601px;top:3124px;width:439px;height:46px;background:var(--white);border-radius:6px;display:flex;align-items:center;padding:0 3px 0 22px}
.sub-form span{flex:1;font-size:12px;color:#8a8f92;letter-spacing:.5px}
.sub-form b{background:var(--teal);height:38px;width:118px;border-radius:4px;display:flex;align-items:center;justify-content:center;font-family:"Lexend",sans-serif;font-size:13px;color:var(--ink)}
.rule{left:111px;top:3217px;width:978px;height:1px;background:#5a5d60}
.col{top:3268px;color:var(--white)}
.col h4{font-family:"Lexend",sans-serif;font-size:20px;font-weight:600;margin-bottom:18px}
.col ul{list-style:none;font-size:15px}
.col li{line-height:27.6px;display:flex;align-items:center;gap:8px}
.contact li{align-items:flex-start;line-height:21px;margin-bottom:14px}
.contact li svg{margin-top:3px;flex:none}
.f-brand{left:880px;top:3270px;display:flex;align-items:center;gap:12px}
.f-brand .mark{width:36px;height:36px;border:3px solid var(--white);border-radius:6px}
.f-brand .name{font-family:"Lexend",sans-serif;font-size:34px;color:var(--teal);line-height:1}
.f-blurb{left:885px;top:3345px;width:210px;font-size:12px;line-height:18px;color:var(--white)}
.socials{left:884px;top:3407px;display:flex;gap:22px}
.socials span{width:28px;height:28px;border:1.5px solid var(--white);border-radius:5px}
.copy{left:0;top:3497px;width:1200px;display:flex;align-items:center;justify-content:center;gap:18px;font-size:11.5px;color:var(--white)}
.copy i{display:block;width:310px;height:1px;background:#6a6d70}
</style>
</head>
<body>

<!-- hero -->
<div class="abs hero-rim"></div>
<header class="abs hero">
  <div class="abs hero-photo" role="img" aria-label="Photo of a clinician in blue scrubs examining the arm and shoulder of a smiling male patient"></div>
  <div class="abs hero-fade"></div>
</header>
<div class="abs brand"><span class="mark"></span><span class="name">brightpath</span></div>
<nav class="abs nav">
  <span class="active">Home</span><span>About</span><span>Services</span><span>For Patients</span>
</nav>
<div class="btn nav-cta">Contact Us</div>
<div class="abs eyebrow hero-eyebrow">Your partner in health</div>
<h1 class="abs head hero-title">Sports Medicine services<br>now available at our<br>Lakeview location</h1>
<p class="abs hero-sub">Book your appointment when it's convenient for you, even<br>if you don't have a family doctor.</p>
<div class="btn hero-btn">Book Online</div>

<!-- about -->
<div class="abs about-art"><span class="sq"></span><span class="word">brightpath</span></div>
<div class="abs eyebrow about-eyebrow">Welcome to Brightpath Care Clinics</div>
<h2 class="abs head about-title">About Brightpath Care Clinics</h2>
<div class="abs about-copy">
  <p>Neque porro quisquam est, qui dolorem ipsum quia dolor sit amet, consectetur, adipisci velit, sed quia non numquam eius modi tempora incidunt ut labore et dolore magnam aliquam quaerat voluptatem.</p>
  <p>Ut enim ad minima veniam, quis nostrum exercitationem ullam corporis suscipit laboriosam, nisi ut iure reprehenderit qui aliquid ex ea commodi consequatur.</p>
</div>
<div class="btn about-btn">Read More</div>

<!-- services -->
<div class="abs eyebrow svc-eyebrow">What we do</div>
<h2 class="abs head svc-title">Our Services</h2>
<div class="abs svc-arrows">
  <svg width="36" height="24" viewBox="0 0 36 24"><path d="M34 12H3M13 2 3 12l10 10" fill="none" stroke="#8a8d90" stroke-width="2.5"/></svg>
  <svg width="36" height="24" viewBox="0 0 36 24"><path d="M2 12h31M23 2l10 10-10 10" fill="none" stroke="#111" stroke-width="2.5"/></svg>
</div>
<article class="abs card c1">
  <div class="photo" role="img" aria-label="Photo of a smiling woman with glasses speaking with a colleague"></div><div class="shade"></div>
  <div class="txt"><h3>Voluptatem Accusantium Doloremque</h3>
  <svg width="26" height="20" viewBox="0 0 26 20"><path d="M2 10h21M15 2l8 8-8 8" fill="none" stroke="#fff" stroke-width="2.5"/></svg></div>
</article>
<article class="abs card c2">
  <div class="photo" role="img" aria-label="Photo of a female doctor with a stethoscope reviewing a clipboard with a patient"></div><div class="shade"></div>
  <div class="txt"><h3>Totamrem Aperiam</h3><p>Duis aute irure dolor in reprehenderit in voluptate velit esse cillum dolore eu fugiat nulla pariatur.</p>
  <svg width="26" height="20" viewBox="0 0 26 20"><path d="M2 10h21M15 2l8 8-8 8" fill="none" stroke="#fff" stroke-width="2.5"/></svg></div>
</article>
<article class="abs card c3">
  <div class="photo" role="img" aria-label="Photo of a doctor checking on a patient resting beside an IV stand"></div><div class="shade"></div>
  <div class="txt"><h3>Quis Autemvel Eumiure Reprehenderit</h3>
  <svg width="26" height="20" viewBox="0 0 26 20"><path d="M2 10h21M15 2l8 8-8 8" fill="none" stroke="#fff" stroke-width="2.5"/></svg></div>
</article>

<!-- happening -->
<div class="abs eyebrow hap-eyebrow">Easy access to care when you need it</div>
<h2 class="abs head hap-title">Exciting Things Are Happening!</h2>
<p class="abs hap-copy">Brightpath Care Clinics continues to create options that better suit your lifestyle. Book your appointment when it's convenient for you, even if you don't have a family doctor.</p>
<ul class="abs hap-list">
  <li><svg width="14" height="13" viewBox="0 0 14 13"><path d="M0 0 14 6.5 0 13 4 6.5z" fill="#111"/></svg>Brightpath Care Clinics is continually adding and improving our services</li>
  <li><svg width="14" height="13" viewBox="0 0 14 13"><path d="M0 0 14 6.5 0 13 4 6.5z" fill="#111"/></svg>To provide patients with access to comprehensive care under one roof</li>
  <li><svg width="14" height="13" viewBox="0 0 14 13"><path d="M0 0 14 6.5 0 13 4 6.5z" fill="#111"/></svg>Renovations have begun at our Ridgeway location!</li>
  <li><svg width="14" height="13" viewBox="0 0 14 13"><path d="M0 0 14 6.5 0 13 4 6.5z" fill="#111"/></svg>Speak with your healthcare provider</li>
  <li><svg width="14" height="13" viewBox="0 0 14 13"><path d="M0 0 14 6.5 0 13 4 6.5z" fill="#111"/></svg>we renovate so please pay attention to the signage guiding you to your physicians assistant.</li>
</ul>
<div class="btn hap-btn">Book Your Appointment</div>
<div class="abs hap-photo" role="img" aria-label="Photo of a smiling man in a white shirt holding a payment card and a laptop"></div>
<div class="abs dot" style="left:743px;top:2100px"><svg width="10" height="14" viewBox="0 0 10 14"><path d="M8 1 2 7l6 6" fill="none" stroke="#999" stroke-width="1.8"/></svg></div>
<div class="abs dot" style="left:1057px;top:2100px"><svg width="10" height="14" viewBox="0 0 10 14"><path d="m2 1 6 6-6 6" fill="none" stroke="#999" stroke-width="1.8"/></svg></div>

<!-- faq -->
<section class="abs faq" role="img" aria-label="Soft teal background with a faint clinic interior"></section>
<div class="abs eyebrow faq-eyebrow">Brightpath Care Clinics</div>
<h2 class="abs head faq-title">Frequently Asked Qusetions</h2>
<div class="abs q q1">
  <svg width="20" height="16" viewBox="0 0 20 16"><path d="M1 8h16M11 2l6 6-6 6" fill="none" stroke="#133035" stroke-width="2"/></svg>
  <span class="label">Excepteur sint occaecat cupidatat non proident, sunt?</span>
  <span class="pm"><svg width="16" height="16" viewBox="0 0 16 16"><path d="M8 1v14M1 8h14" stroke="#2fd0dc" stroke-width="3"/></svg></span>
</div>
<div class="abs qopen">
  <div class="row">
    <svg width="20" height="16" viewBox="0 0 20 16"><path d="M1 8h16M11 2l6 6-6 6" fill="none" stroke="#133035" stroke-width="2"/></svg>
    <span class="label" style="flex:1;margin-left:10px">Itaque earum rerum hic tenetur a sapiente delectus?</span>
    <span class="pm"><svg width="16" height="4" viewBox="0 0 16 4"><path d="M1 2h14" stroke="#fff" stroke-width="3"/></svg></span>
  </div>
  <p>At vero eos et accusamus et iusto odio dignissimos ducimus qui blanditiis praesentium voluptatum deleniti atque corrupti quos dolores et quas molestias excepturi sint occaecati cupiditate non provident, similique sunt in culpa qui officia deserunt mollitia animi, id est laborum et dolorum fuga. Et harum quidem rerum facilis est et expedita distinctio. Nam libero tempore, cum soluta nobis est eligendi optio cumque nihil impedit quo minus voluptas assumenda est, omnis dolor repellendus.</p>
</div>
<div class="abs q q3">
  <svg width="20" height="16" viewBox="0 0 20 16"><path d="M1 8h16M11 2l6 6-6 6" fill="none" stroke="#133035" stroke-width="2"/></svg>
  <span class="label">Vel illum qui dolorem eum fugiat quo voluptas nulla pariatur?</span>
  <span class="pm"><svg width="16" height="16" viewBox="0 0 16 16"><path d="M8 1v14M1 8h14" stroke="#2fd0dc" stroke-width="3"/></svg></span>
</div>
<div class="btn view-btn">View More</div>

<!-- footer -->
<div class="abs foot-rim"></div>
<div class="abs foot-rim2"></div>
<footer class="abs foot"></footer>
<h3 class="abs head sub-title">Subscribe for Join us</h3>
<div class="abs sub-form"><span>Enter Your Email</span><b>SUBSCRIBE</b></div>
<div class="abs rule"></div>

<div class="abs col contact" style="left:113px">
  <h4>Contact Us</h4>
  <ul>
    <li><svg width="14" height="18" viewBox="0 0 14 18"><path d="M7 1a6 6 0 0 0-6 6c0 4.5 6 10 6 10s6-5.5 6-10a6 6 0 0 0-6-6z" fill="#fff"/><circle cx="7" cy="7" r="2.2" fill="#050607"/></svg><span>Brightpath Care Clinics<br>United States</span></li>
    <li><svg width="14" height="14" viewBox="0 0 14 14"><path d="M3 1 5.5 4 4 5.8a8 8 0 0 0 4.2 4.2L10 8.5l3 2.5-1.5 2C6.5 13 1 7.5 1 2.5z" fill="#fff"/></svg><span>250.555.0147</span></li>
    <li><svg width="14" height="12" viewBox="0 0 14 12"><rect x="1" y="1.5" width="12" height="9" fill="#fff"/><path d="m1 2 6 4.5L13 2" fill="none" stroke="#050607" stroke-width="1.2"/></svg><span>hello@brightpathcareclinics.ca</span></li>
  </ul>
</div>
<div class="abs col" style="left:419px">
  <h4>Quick Links</h4>
  <ul><li>→ Home</li><li>→ Services</li><li>→ About us</li><li>→ Testimonials</li><li>→ Contact</li></ul>
</div>
<div class="abs col" style="left:661px">
  <h4>Help Center</h4>
  <ul><li>→ FAQ</li><li>→ Terms</li><li>→ Privacy Policy</li><li>→ Support Center</li><li>→ Conditions</li></ul>
</div>
<div class="abs f-brand"><span class="mark"></span><span class="name">brightpath</span></div>
<p class="abs f-blurb">Book your appointment when it's convenient for you, even if you don't have a family doctor.</p>
<div class="abs socials"><span></span><span></span><span></span></div>
<div class="abs copy"><i></i><span>Copyrights@2022.Brightpath Care Clinics.All Rights Reserved</span><i></i></div>

</body>
</html>
```